Design eines Hausetiketts für traditionelles Weingut
Zielgruppe
Wir das Familienweingut Brandauer in Gimbsheim/Rheinhessen sind ein traditionelles Weingut das seine Reben selbst kultiviert und die Weine auch selbst ausbaut. Wir haben jeden Schritt in der Weinherstellung selbst in der Hand und vermarkten den Wein dann an unsere Privatkunden. Unsere Kundenstruktur sieht folgendermaßen aus: Wir haben 100% Privatkunden die unseren Wein konsumieren. Da jetzt die nächste Generation in den Weinbaubetrieb einsteigt und auch Ideen hat möchten wir ein Hausetikett einführen. Im Moment haben wir noch sehr viele unterschiedliche Etiketten und kein Hausetikett. Da die Verlagsetiketten immer seltener zu unseren Vorstellungen passen, möchten wir hier auf diesem Wege ein Hausetikett anfertigen lassen. Generell möchten wir unseren Außenauftritt komplett modernisieren. Sie können sich über die Vielfalt in unserem Betrieb unter www.weingut-brandauer-beispiel.de einen Überblick verschaffen. Langfristig gesehen wollen wir aber unsere Weinkarte verkleinern.
Aufgabenstellung
Wir haben uns vor ca. 1,5 Jahren hier auf dieser Website bereits ein Logo designen lassen. Es wäre schön wenn man das Logo bei den Entwürfen für die Etiketten berücksichtigen würde. Das wäre aber KEIN MUSS. Auch wäre es gut wenn man das ,,Wein' bei unserem Namen weglassen könnte.
Das Etikett sollte aus Vorder-und Rückenetikett bestehen und edel wirken. Vorne sollte die Rebsorte und die Geschmacksangabe stehen. Der Rest sollte auf das Rückenetikett.
Das Vorderetikett sollte ein richtiger Eyecatcher sein und im Supermarkt z.B. aus vielen anderen herausstechen. Das wäre ganz wichtig.
Man kann bei den Farben unterscheiden in 3 Konzepte.
Literwein als einsteiger Wein
Dann die Gutsweine und zum Schluss die Lagenweine. Alles Farblich oder im design etwas abgesetzt.

```html
<!DOCTYPE html>
<html lang="de">
<head>
<meta charset="utf-8">
<title>Brandauer – Hausetiketten</title>
<link rel="stylesheet" href="https://fonts.googleapis.com/css2?family=Zilla+Slab:wght@700&family=Oswald:wght@400&family=Roboto:wght@500&display=swap">
<style>
  :root {
    --page: #ffffff;
    --gold: #b8955e;
    --berry: #c3232b;
    --white: #ffffff;
    --night: #04070d;
    --blue: #2d6cc2;
  }
  * { margin: 0; padding: 0; box-sizing: border-box; }
  html, body { width: 1200px; height: 2368px; overflow: hidden; background: var(--page); }
  .sheet { position: relative; width: 1200px; height: 2368px; }

  .label { position: absolute; left: 0; width: 1200px; overflow: hidden; color: var(--white); }
  .label--classic { top: 30px; height: 753px; }
  .label--red { top: 832px; height: 727px; }
  .label--white { top: 1612px; height: 729px; }

  .classic-upper {
    position: absolute; left: 0; top: 0; width: 100%; height: 385px;
    background: radial-gradient(ellipse 55% 110% at 50% 100%, #ffffff 0%, #f0f0f0 45%, #b9b9b9 100%);
  }
  .classic-lower {
    position: absolute; left: 0; top: 385px; width: 100%; height: 368px;
    background: radial-gradient(ellipse 55% 130% at 50% 0%, #000 0%, #0d0d0d 55%, #353535 100%);
  }
  .classic-shelf {
    position: absolute; left: 197px; top: 382px; width: 766px; height: 4px;
    background: var(--white); box-shadow: 0 -6px 18px rgba(255,255,255,.9);
  }

  .label--red, .label--white {
    background: radial-gradient(ellipse 60% 85% at 55% 0%, var(--blue) 0%, #1b3f78 40%, #0a1425 72%, var(--night) 100%);
  }
  .waves { position: absolute; inset: 0; width: 100%; height: 100%; }

  .brand { position: absolute; left: 0; width: 100%; text-align: center; }
  .brand-dot {
    display: block; margin: 0 auto 50px; width: 96px; height: 96px;
    border-radius: 50%; background: var(--berry);
  }
  .brand-name {
    font-family: "Zilla Slab", Georgia, serif; font-weight: 700;
    font-size: 110px; letter-spacing: 6px; color: var(--gold); line-height: 1;
  }

  .wine { position: absolute; left: 0; width: 100%; text-align: center;
    font-family: "Zilla Slab", Georgia, serif; font-weight: 700; line-height: 1.1; }
  .wine-type { font-size: 56px; }
  .wine-detail { font-size: 54px; }
  .wine-year { font-size: 54px; }

  .spec { position: absolute; font-family: "Oswald", "Arial Narrow", sans-serif;
    font-size: 46px; line-height: 1; }
  .apnr { position: absolute; left: 0; width: 100%; text-align: center;
    font-family: "Roboto", Arial, sans-serif; font-weight: 500; font-size: 20px; letter-spacing: .5px; }
</style>
</head>
<body>
<main class="sheet">

  <section class="label label--classic" aria-label="Etikett Rotwein, helle Variante">
    <div class="classic-upper"></div>
    <div class="classic-lower"></div>
    <div class="classic-shelf"></div>
    <div class="brand" style="top:120px">
      <span class="brand-dot"></span>
      <div class="brand-name">BRANDAUER</div>
    </div>
    <div class="wine" style="top:480px">
      <div class="wine-type">ROTWEIN</div>
      <div class="wine-year">2019</div>
    </div>
    <div class="spec" style="left:0;top:665px">12,5%</div>
    <div class="apnr" style="top:705px;left:-17px">A.P.Nr. 1 208 517 046 22</div>
    <div class="spec" style="right:57px;top:665px">0.75L</div>
  </section>

  <section class="label label--red" aria-label="Etikett Rotwein, blaue Variante">
    <svg class="waves" viewBox="0 0 1200 727" preserveAspectRatio="none" aria-hidden="true">
      <defs>
        <linearGradient id="redBand" x1="0" y1="0" x2="1" y2="1">
          <stop offset="0" stop-color="#3a0d14"/>
          <stop offset=".45" stop-color="#5e1b2a"/>
          <stop offset="1" stop-color="#150306"/>
        </linearGradient>
        <linearGradient id="redDeep" x1="0" y1="0" x2="1" y2="0">
          <stop offset="0" stop-color="#1a0305"/>
          <stop offset=".35" stop-color="#4d1016"/>
          <stop offset="1" stop-color="#0c0102"/>
        </linearGradient>
      </defs>
      <path d="M0,380 C250,340 600,370 850,365 C1000,360 1120,300 1200,250 L1200,727 L0,727 Z" fill="url(#redBand)"/>
      <path d="M0,465 C250,430 420,520 560,580 C700,640 860,610 980,510 C1080,430 1150,360 1200,310 L1200,727 L0,727 Z" fill="url(#redDeep)"/>
    </svg>
    <div class="brand" style="top:110px;left:24px">
      <span class="brand-dot"></span>
      <div class="brand-name">BRANDAUER</div>
    </div>
    <div class="wine" style="top:460px;left:1px">
      <div class="wine-type">ROTWEIN</div>
      <div class="wine-year">2019</div>
    </div>
    <div class="spec" style="left:38px;top:640px">12,5%</div>
    <div class="apnr" style="top:666px;left:3px">A.P.Nr. 1 208 517 046 22</div>
    <div class="spec" style="right:55px;top:640px">0.75L</div>
  </section>

  <section class="label label--white" aria-label="Etikett Weißwein Riesling">
    <svg class="waves" viewBox="0 0 1200 729" preserveAspectRatio="none" aria-hidden="true">
      <defs>
        <linearGradient id="tealBand" x1="0" y1="0" x2="0" y2="1">
          <stop offset="0" stop-color="#17585c"/>
          <stop offset=".55" stop-color="#0c2a30"/>
          <stop offset="1" stop-color="#04090c"/>
        </linearGradient>
        <linearGradient id="tealDeep" x1="0" y1="0" x2="0" y2="1">
          <stop offset="0" stop-color="#0f3940"/>
          <stop offset="1" stop-color="#030709"/>
        </linearGradient>
      </defs>
      <path d="M0,330 C120,300 230,305 330,370 C430,440 520,450 700,440 C850,430 950,320 1080,310 C1140,305 1180,310 1200,315 L1200,729 L0,729 Z" fill="url(#tealBand)" opacity=".9"/>
      <path d="M0,440 C150,410 300,480 420,570 C520,640 650,610 780,530 C900,450 1000,370 1200,340 L1200,729 L0,729 Z" fill="url(#tealDeep)"/>
    </svg>
    <div class="brand" style="top:110px;left:24px">
      <span class="brand-dot"></span>
      <div class="brand-name">BRANDAUER</div>
    </div>
    <div class="wine" style="top:462px;left:1px">
      <div class="wine-type">WEISSWEIN</div>
      <div class="wine-detail">Riesling</div>
      <div class="wine-year">2019</div>
    </div>
    <div class="spec" style="left:38px;top:642px">13,0%</div>
    <div class="apnr" style="top:680px;left:3px">A.P.Nr. 1 208 517 046 22</div>
    <div class="spec" style="right:55px;top:642px">0.75L</div>
  </section>

</main>
</body>
</html>
```